Business Card Design

New business card design

Target Market(s)

Residential & Commercial Property Managers

Industry/Entity Type

Plumbing Services

Contact Information for Business Card

Name - Rowan Keddle, title - Director, Phone Number - 0431 286 517, email - rowan@tbk-plumbing.com.au, Company ABN - 73 215 904 386,

Font styles to use
Sans Serif

Colors
0054AA
0677BA
7BADD7
CADEEF
E8F1F8

```html
<!DOCTYPE html>
<html lang="en">
<head>
<meta charset="utf-8">
<title>TBK Plumbing Services – Business Card</title>
<link rel="stylesheet" href="https://fonts.googleapis.com/css2?family=Montserrat:wght@700;800&family=Poppins:wght@300;400;500;700&display=swap">
<style>
  :root{
    --stage:#e4e4e4;
    --navy:#020833;
    --pipe:#0d1b4c;
    --band:#1461ad;
    --band-deep:#0054aa;
    --splash:#2bb3e8;
    --splash-mid:#1d85c8;
    --sky:#1fb0ea;
    --white:#ffffff;
    --rule:#7badd7;
  }
  *{margin:0;padding:0;box-sizing:border-box}
  html,body{width:1200px;height:1111px;overflow:hidden;background:var(--stage)}
  body{position:relative;font-family:"Poppins",sans-serif;color:var(--white)}
  .card{position:absolute;top:145px;width:470px;height:822px;background:var(--navy);overflow:hidden;box-shadow:10px 12px 18px rgba(0,0,0,.28)}
  .card--front{left:104px}
  .card--back{left:626px}
  .card__art{position:absolute;inset:0;width:470px;height:822px}
  .brand{position:absolute;left:0;right:0;text-align:center}
  .brand__name{display:block;font-family:"Poppins",sans-serif;font-weight:300;color:var(--white);line-height:1;letter-spacing:6px}
  .brand__tagline{display:block;font-family:"Poppins",sans-serif;font-weight:400;font-size:12px;letter-spacing:13px;color:var(--white)}
  .card--front .brand{top:248px}
  .card--front .brand__name{font-size:112px}
  .card--front .brand__tagline{margin-top:18px}
  .card--back .brand{top:52px}
  .card--back .brand__name{font-size:88px}
  .card--back .brand__tagline{margin-top:14px;font-size:11px;letter-spacing:12px}
  .person{position:absolute;left:56px;top:232px}
  .person__name{font-family:"Montserrat",sans-serif;font-weight:800;font-size:38px;line-height:1;letter-spacing:-.5px;white-space:nowrap}
  .person__surname{color:var(--sky)}
  .person__title{margin-top:12px;font-size:17px;letter-spacing:3.5px;font-weight:400}
  .divider{position:absolute;left:56px;top:325px;width:357px;height:1px;background:var(--rule);opacity:.7}
  .contact{position:absolute;left:59px;top:345px}
  .contact__pill{position:absolute;left:0;top:0;width:24px;height:76px;border-radius:12px;overflow:hidden;border:1px solid var(--sky)}
  .contact__pill span{display:flex;align-items:center;justify-content:center;height:50%}
  .contact__pill .top{background:var(--sky)}
  .contact__pill .bottom{background:var(--band)}
  .contact__list{position:absolute;left:38px;top:4px;list-style:none;font-size:20px;line-height:35px;white-space:nowrap}
  .abn{position:absolute;left:60px;top:440px;display:flex;align-items:center;white-space:nowrap}
  .abn__label{display:inline-block;padding:0 14px;height:32px;line-height:31px;border-radius:16px;border:1.5px solid var(--sky);background:var(--band);font-weight:700;font-size:18px}
  .abn__number{margin-left:13px;font-weight:700;font-size:20px;letter-spacing:1px}
</style>
</head>
<body>

<section class="card card--front">
  <svg class="card__art" viewBox="0 0 470 822" aria-hidden="true">
    <defs>
      <linearGradient id="pipes-front" x1="0" y1="0" x2="1" y2="0">
        <stop offset="0" stop-color="#0d1b4c" stop-opacity="0"/>
        <stop offset="1" stop-color="#0d1b4c" stop-opacity=".9"/>
      </linearGradient>
      <radialGradient id="splash-front" cx=".6" cy=".55" r=".55">
        <stop offset="0" stop-color="#2bb3e8"/>
        <stop offset=".7" stop-color="#1d85c8" stop-opacity=".85"/>
        <stop offset="1" stop-color="#1d85c8" stop-opacity="0"/>
      </radialGradient>
    </defs>
    <g role="img" aria-label="Faint pipework background illustration">
      <rect x="230" y="0" width="240" height="760" fill="url(#pipes-front)"/>
    </g>
    <g role="img" aria-label="Water splash illustration">
      <rect x="180" y="530" width="290" height="260" fill="url(#splash-front)"/>
    </g>
    <path d="M28,822 C90,760 170,728 270,738 C370,748 430,700 470,650 L470,822 Z" fill="var(--band)"/>
  </svg>
  <div class="brand">
    <span class="brand__name">tbk</span>
    <span class="brand__tagline">plumbing services</span>
  </div>
</section>

<section class="card card--back">
  <svg class="card__art" viewBox="0 0 470 822" aria-hidden="true">
    <defs>
      <linearGradient id="pipes-back" x1="0" y1="0" x2="0" y2="1">
        <stop offset="0" stop-color="#0d1b4c" stop-opacity="0"/>
        <stop offset=".5" stop-color="#0d1b4c" stop-opacity=".8"/>
        <stop offset="1" stop-color="#0d1b4c" stop-opacity=".9"/>
      </linearGradient>
      <radialGradient id="splash-back" cx=".6" cy=".55" r=".55">
        <stop offset="0" stop-color="#2bb3e8"/>
        <stop offset=".7" stop-color="#1d85c8" stop-opacity=".85"/>
        <stop offset="1" stop-color="#1d85c8" stop-opacity="0"/>
      </radialGradient>
    </defs>
    <g role="img" aria-label="Faint pipework background illustration">
      <rect x="0" y="400" width="470" height="360" fill="url(#pipes-back)"/>
    </g>
    <g role="img" aria-label="Water splash illustration">
      <rect x="180" y="530" width="290" height="260" fill="url(#splash-back)"/>
    </g>
    <path d="M28,822 C90,760 170,728 270,738 C370,748 430,700 470,650 L470,822 Z" fill="var(--band)"/>
  </svg>

  <div class="brand">
    <span class="brand__name">tbk</span>
    <span class="brand__tagline">plumbing services</span>
  </div>

  <div class="person">
    <h1 class="person__name">Rowan <span class="person__surname">Keddle</span></h1>
    <p class="person__title">DIRECTOR</p>
  </div>

  <div class="divider"></div>

  <div class="contact">
    <div class="contact__pill">
      <span class="top">
        <svg width="12" height="12" viewBox="0 0 24 24" aria-hidden="true"><path fill="#fff" d="M6.6 10.8a15.1 15.1 0 0 0 6.6 6.6l2.2-2.2a1 1 0 0 1 1-.25 11.4 11.4 0 0 0 3.6.57 1 1 0 0 1 1 1V20a1 1 0 0 1-1 1A17 17 0 0 1 3 4a1 1 0 0 1 1-1h3.5a1 1 0 0 1 1 1c0 1.25.2 2.45.57 3.57a1 1 0 0 1-.25 1z"/></svg>
      </span>
      <span class="bottom">
        <svg width="13" height="10" viewBox="0 0 26 20" aria-hidden="true"><rect x="1" y="1" width="24" height="18" rx="2" fill="#fff"/><path d="M2 3l11 8 11-8" fill="none" stroke="#1461ad" stroke-width="2"/></svg>
      </span>
    </div>
    <ul class="contact__list">
      <li>0431 286 517</li>
      <li>rowan@tbk-plumbing.com.au</li>
    </ul>
  </div>

  <div class="abn">
    <span class="abn__label">Company ABN</span>
    <span class="abn__number">73 215 904 386</span>
  </div>
</section>

</body>
</html>
```